Summit Ridge Business Card

Side 1: Summit Ridge Logo (logo without Maltese cross) with industrial rope rescue related theme. Our company services - TRAINING - Fire Training, Confined Space Rescue Training, Rope Rescue training, Hazmat Training, Incident Command, EMS, Pump Operations Training. Website - summitridgeexample.com.
Side 2: Summit Ridge Fire Department Logo (logo with Maltese cross) with Firefighter related theme. Company (division) services - FIELD SERVICES - Fire Department, Stand-by Rescue, Safety, EMS, Planning. "Supporting the Emergency Response Community Since 1967"

Add contact information wherever it makes since (Name, Email, Phone).
I would like it to represent the Summit Ridge Fire Department Logo as a division not as a separate entity without saying it, possibly by depicting it in the background of Side 2 instead of being a standalone picture like the logo on Side 1.

```html
<!DOCTYPE html>
<html lang="en">
<head>
<meta charset="utf-8">
<title>Summit Ridge Business Card</title>
<link rel="stylesheet" href="https://fonts.googleapis.com/css2?family=Montserrat:wght@400;500;600;700;800&display=swap">
<style>
  :root {
    --backdrop: #1a1a1c;
    --card: #262628;
    --card-deep: #1f1f21;
    --red: #e3202a;
    --red-deep: #5a1417;
    --white: #ffffff;
    --muted: #d4d4d4;
    --soft: #9a9a9c;
  }
  * { margin: 0; padding: 0; box-sizing: border-box; }
  html, body {
    width: 1200px; height: 900px; overflow: hidden;
    background: var(--backdrop);
    font-family: "Montserrat", Arial, sans-serif;
  }
  .canvas { position: relative; width: 1200px; height: 900px; }

  .card {
    position: absolute;
    width: 600px; height: 340px;
    background: var(--card);
    border-radius: 18px;
    overflow: hidden;
    border-bottom: 4px solid var(--red);
    box-shadow: 0 18px 40px rgba(0,0,0,.5);
  }
  .card-front { left: 60px; top: 60px; }
  .card-back { left: 540px; top: 490px; }

  .theme-art {
    position: absolute; inset: 0;
  }
  .card-front .theme-art {
    background: radial-gradient(ellipse at 88% 30%, rgba(90,20,23,.55) 0%, rgba(38,38,40,0) 60%);
  }
  .card-back .theme-art {
    background: radial-gradient(ellipse at 30% 20%, rgba(90,20,23,.45) 0%, rgba(38,38,40,0) 55%);
  }

  .brand-name {
    color: var(--red);
    font-weight: 800;
    text-transform: uppercase;
    white-space: nowrap;
  }
  .brand-mark { border-radius: 50%; background: var(--red); flex: none; }

  /* Front */
  .front-lockup {
    position: absolute; left: 0; right: 0; top: 92px;
    display: flex; align-items: center; justify-content: center; gap: 14px;
  }
  .front-lockup .brand-mark { width: 18px; height: 18px; }
  .front-lockup .brand-name { font-size: 42px; letter-spacing: 2px; }

  .rule-row {
    position: absolute; left: 0; right: 0; top: 160px;
    display: flex; align-items: center; justify-content: center; gap: 14px;
  }
  .rule-row .rule { width: 90px; height: 2px; background: var(--red); }
  .rule-row .label {
    color: var(--white); font-weight: 700; font-size: 15px; letter-spacing: 4px;
  }

  .training-list {
    position: absolute; left: 50px; right: 50px; top: 196px;
    list-style: none;
    display: flex; flex-wrap: wrap; justify-content: center; gap: 6px 18px;
    color: var(--muted); font-size: 12px; font-weight: 500;
  }
  .training-list li { display: flex; align-items: center; gap: 7px; }
  .training-list li::before {
    content: ""; width: 5px; height: 5px; background: var(--red); flex: none;
  }

  .front-web {
    position: absolute; left: 0; right: 0; bottom: 20px;
    text-align: center; color: var(--white); font-size: 13px; letter-spacing: .5px;
  }

  /* Back */
  .back-lockup {
    position: absolute; right: 36px; top: 26px;
    text-align: right;
  }
  .back-lockup .row { display: flex; align-items: center; gap: 8px; justify-content: flex-end; }
  .back-lockup .brand-mark { width: 10px; height: 10px; }
  .back-lockup .brand-name { font-size: 19px; letter-spacing: 1px; }
  .back-lockup .division {
    color: var(--soft); font-size: 10px; font-weight: 600;
    letter-spacing: 2px; text-transform: uppercase; margin-top: 3px;
  }

  .services {
    position: absolute; right: 36px; top: 82px; width: 230px;
    text-align: right;
  }
  .services-title {
    color: var(--red); font-weight: 700; font-size: 12px; letter-spacing: 3px;
    margin-bottom: 5px;
  }
  .services-list {
    list-style: none; color: var(--muted); font-size: 11px; line-height: 1.55;
  }

  .name-band {
    position: absolute; left: 0; top: 116px;
    width: 320px; height: 62px;
    background: var(--red);
    clip-path: polygon(0 0, 100% 0, 82% 100%, 0 100%);
    padding: 9px 0 0 34px;
    color: var(--white);
  }
  .person-name { font-weight: 700; font-size: 22px; line-height: 1.1; }
  .person-title { font-weight: 400; font-size: 12px; margin-top: 3px; }

  .contact-list {
    position: absolute; left: 34px; top: 210px;
    list-style: none; color: var(--muted); font-size: 12px;
  }
  .contact-list li { display: flex; align-items: center; gap: 10px; height: 24px; }
  .contact-list svg { width: 13px; height: 13px; flex: none; }
  .icon-fill { fill: var(--red); }
  .icon-line { fill: none; stroke: var(--red); stroke-width: 2.2; }

  .address {
    position: absolute; right: 36px; top: 196px;
    text-align: right; font-style: normal;
    color: var(--muted); font-size: 11px; line-height: 1.45;
  }

  .tagline {
    position: absolute; right: 36px; top: 254px; width: 250px;
    text-align: right; color: var(--white);
    font-size: 10px; font-weight: 600; line-height: 1.35;
  }

  .web-band {
    position: absolute; right: 0; bottom: 0;
    width: 290px; height: 40px;
    background: var(--red);
    clip-path: polygon(6% 0, 100% 0, 100% 100%, 0 100%, 0 30%);
    color: var(--white); font-size: 13px;
    display: flex; align-items: center; justify-content: flex-end;
    padding-right: 34px;
  }
</style>
</head>
<body>
<main class="canvas">

  <section class="card card-front" aria-label="Card front">
    <div class="theme-art" role="img" aria-label="Industrial rope rescue scene with a rescuer on a line"></div>

    <div class="front-lockup">
      <span class="brand-mark"></span>
      <span class="brand-name">Summit Ridge</span>
    </div>

    <div class="rule-row">
      <span class="rule"></span>
      <span class="label">TRAINING</span>
      <span class="rule"></span>
    </div>

    <ul class="training-list">
      <li>Fire Training</li>
      <li>Confined Space Rescue</li>
      <li>Rope Rescue</li>
      <li>Hazmat</li>
      <li>Incident Command</li>
      <li>EMS</li>
      <li>Pump Operations</li>
    </ul>

    <p class="front-web">www.summitridgeexample.com</p>
  </section>

  <section class="card card-back" aria-label="Card back">
    <div class="theme-art" role="img" aria-label="Firefighter scene with the fire department division emblem in the background"></div>

    <div class="back-lockup">
      <div class="row">
        <span class="brand-mark"></span>
        <span class="brand-name">Summit Ridge</span>
      </div>
      <p class="division">Fire Department</p>
    </div>

    <div class="services">
      <p class="services-title">FIELD SERVICES</p>
      <ul class="services-list">
        <li>Fire Department &middot; Stand-by Rescue</li>
        <li>Safety &middot; EMS &middot; Planning</li>
      </ul>
    </div>

    <div class="name-band">
      <p class="person-name">Daniel Harlow</p>
      <p class="person-title">Managing Director</p>
    </div>

    <ul class="contact-list">
      <li>
        <svg viewBox="0 0 24 24" aria-hidden="true"><path class="icon-fill" d="M6.6 10.8a15.1 15.1 0 0 0 6.6 6.6l2.2-2.2c.3-.3.7-.4 1-.2 1.1.4 2.3.6 3.6.6.6 0 1 .4 1 1V20c0 .6-.4 1-1 1A17 17 0 0 1 3 4c0-.6.4-1 1-1h3.5c.6 0 1 .4 1 1 0 1.3.2 2.5.6 3.6.1.3 0 .7-.2 1z"/></svg>
        <span>877-555-0142</span>
      </li>
      <li>
        <svg viewBox="0 0 24 24" aria-hidden="true"><rect class="icon-line" x="3" y="5" width="18" height="14" rx="1"/><path class="icon-line" d="M3 6l9 7 9-7"/></svg>
        <span>info@summitridgeexample.com</span>
      </li>
      <li>
        <svg viewBox="0 0 24 24" aria-hidden="true"><circle class="icon-line" cx="12" cy="12" r="9"/><path class="icon-line" d="M3 12h18M12 3c3 3 3 15 0 18M12 3c-3 3-3 15 0 18"/></svg>
        <span>www.summitridgeexample.com</span>
      </li>
    </ul>

    <address class="address">
      218 Cedar Mill Road<br>
      Hollins ON K2P 4R7
    </address>

    <p class="tagline">Supporting the Emergency Response Community Since 1967</p>

    <div class="web-band">www.summitridgeexample.com</div>
  </section>

</main>
</body>
</html>
```